AGP letterhead

We need a letterhead design for our new company based in Los Angeles called "Amber Gate Pictures". We develop film and television projects. We work with investors, financiers, film production companies, film distribution and sales companies as well as studios. We would like to incorporate our logo (see attached) but make the letterhead simple and elegant. We need to include: logo, company address, phone number and company website.
Updates

Hello designers, Thanks for your submissions. For our letterhead, we are looking for something more simple and elegant. No heavy bars or lines. Make it feel light and clean. Not a lot of ink on the page. Use the logo and contact info but think "clean", "streamlined" and mostly white paper. Looking forward to seeing more... thanks! Amber Gate Pictures team

Target Market(s)

Studio executives, talent agents and agencies, financiers, investors.

Industry/Entity Type

It Company

Requirements
Must have
• Amber Gate Pictures logo (see attached). Logo may be cropped and altered appropriately for elegant letterhead design.
• Please include:
• COMPANY ADDRESS:
• Tolvane Arts Park
• 2850 Delmore Street
• Crest Hall, 2nd Floor
• Larkin Shores, CA 90412
• COMPANY WEBSITE:
• www.ambergatepicturesco.example
• COMPANY PHONE NUMBER:
• 555-604-2187

```html
<!DOCTYPE html>
<html lang="en">
<head>
<meta charset="utf-8">
<title>Amber Gate Pictures — Letterhead</title>
<link rel="stylesheet" href="https://fonts.googleapis.com/css2?family=Open+Sans:wght@400;600&display=swap">
<style>
  :root {
    --backdrop: #e4e4e4;
    --paper: #fbfbfb;
    --brand-blue: #1a9fd0;
    --badge-dark: #0b2a38;
    --band-deep: #0a6c97;
    --band-bright: #16ade6;
    --accent-line: #1aaee6;
    --faint-disc: #efefef;
    --footer-text: #ffffff;
  }
  html, body {
    margin: 0;
    padding: 0;
    width: 950px;
    height: 1200px;
    overflow: hidden;
    background: var(--backdrop);
  }
  .canvas {
    position: relative;
    width: 950px;
    height: 1200px;
  }
  .letterhead {
    position: absolute;
    left: 50px;
    top: 50px;
    width: 850px;
    height: 1100px;
    background: linear-gradient(160deg, #ffffff 0%, var(--paper) 60%, #f5f5f5 100%);
    overflow: hidden;
    font-family: "Open Sans", Arial, sans-serif;
  }
  .brand {
    position: absolute;
    left: 70px;
    top: 24px;
    width: 213px;
    text-align: center;
  }
  .brand-badge {
    display: block;
    width: 124px;
    height: 124px;
    margin: 0 auto;
    border-radius: 50%;
    background: var(--badge-dark);
  }
  .brand-name {
    margin: 14px 0 0;
    font-size: 17px;
    font-weight: 600;
    letter-spacing: 1.5px;
    line-height: 1.25;
    color: var(--brand-blue);
    text-transform: uppercase;
  }
  .center-disc {
    position: absolute;
    left: 255px;
    top: 372px;
    width: 334px;
    height: 334px;
    border-radius: 50%;
    background: var(--faint-disc);
  }
  .footer-wave {
    position: absolute;
    left: 0;
    bottom: 0;
    width: 850px;
    height: 150px;
    display: block;
  }
  .contact {
    position: absolute;
    right: 34px;
    bottom: 12px;
    text-align: right;
    color: var(--footer-text);
    font-size: 15px;
    font-style: normal;
    font-weight: 400;
    line-height: 1.3;
    white-space: nowrap;
  }
  .contact p { margin: 0; }
  .contact .line { margin-bottom: 6px; }
  .contact .icon {
    width: 14px;
    height: 14px;
    vertical-align: -2px;
    margin-right: 5px;
  }
  .contact .address { margin-top: 2px; }
</style>
</head>
<body>
<div class="canvas">
  <div class="letterhead">
    <header class="brand">
      <span class="brand-badge"></span>
      <p class="brand-name">Amber Gate<br>Pictures</p>
    </header>

    <div class="center-disc"></div>

    <svg class="footer-wave" viewBox="0 0 850 150" aria-hidden="true">
      <defs>
        <linearGradient id="bandGradient" x1="0" y1="0" x2="1" y2="0">
          <stop offset="0" stop-color="var(--band-deep)"/>
          <stop offset="1" stop-color="var(--band-bright)"/>
        </linearGradient>
      </defs>
      <path d="M0 72 C250 78 430 42 600 22 C700 11 790 6 850 5" fill="none" stroke="var(--accent-line)" stroke-width="5"/>
      <path d="M0 88 C250 96 450 62 600 38 C700 24 800 16 850 15 L850 150 L0 150 Z" fill="url(#bandGradient)"/>
      <path d="M30 101 C260 100 450 66 620 42 C720 29 800 22 850 21" fill="none" stroke="#ffffff" stroke-width="2"/>
    </svg>

    <address class="contact">
      <p class="line">
        <svg class="icon" viewBox="0 0 14 14" aria-hidden="true"><circle cx="7" cy="7" r="6.2" fill="none" stroke="#fff" stroke-width="1.2"/><path d="M4.6 3.6 L6 5.2 L5.3 6.2 C5.9 7.4 6.7 8.2 7.8 8.7 L8.8 8 L10.4 9.4 L9.4 10.5 C7 10.3 3.9 7.2 3.6 4.6 Z" fill="#fff"/></svg>555-604-2187
      </p>
      <p class="line">
        <svg class="icon" viewBox="0 0 14 14" aria-hidden="true"><g fill="none" stroke="#fff" stroke-width="1"><circle cx="7" cy="7" r="6"/><ellipse cx="7" cy="7" rx="2.6" ry="6"/><path d="M1 7 H13 M2 4 H12 M2 10 H12"/></g></svg>www.ambergatepicturesco.example
      </p>
      <p class="address">Tolvane Arts Park 2850 Delmore Street Crest Hall,<br>2nd Floor Larkin Shores, CA 90412</p>
    </address>
  </div>
</div>
</body>
</html>
```